Financial investment calculator report for real estae - layout & design

I am looking to Create a web report utilizing the attached information. It is an investment calculator report that will be customized report based on an online calculator. Therefore the report will need to be designed in a manner that a backend developer will be able to build off of.

The report will need to be web based but also printed in PDF format. The report will need to include the calculation format as well as be templeted to add a report user unique profile information like Headshot, Business Logo, Name, Telephone number, email etc.

The report should be modern and clean and easy to read and use a modern clean template design. It should be able to be easily color customized by the end user to produce templets in Red, Blue, Green, and Greyscale.

The report should be no more than 3 pages total with out breaking up the sections.

Section One - Cover sheet including agent bio info, Report Title and property address (both prominent), 400 Character space for property description, Property Pictures (3), and a google Maps integration image showing property location, It should also have room for about 100 words for a text disclaimer. (I will provide text soon)

Section Two - Inputs from the calculator

Section 3 - The Four Benefits & Rates of Return

Once I have a completed/approved form I will have about a half dozen forms/reports that will need to be laid out with a similar aesthetic.

Feel free to ask me any questions. Thank You
Milo

Target Market(s)

This report will be produced by real estate agents forvtheir investor clients. It should denote professionalism

Font styles to use
Sans Serif

Colors
0054AA
0677BA
7BADD7
CADEEF
E8F1F8
00AB8E
00BBA5
67D7C9
C6EFE9
E9F9F6
EB3D1F
EC4F4E
F09395
F8D3D4
FCEDEE

```html
<!DOCTYPE html>
<html lang="en">
<head>
<meta charset="UTF-8">
<title>412 Fernwood – Investment Report</title>
<link rel="stylesheet" href="https://fonts.googleapis.com/css2?family=Lato:wght@300;400;700&display=swap">
<style>
  :root{
    --accent:#2400e6;
    --ink:#111111;
    --muted:#444444;
    --rule:#dddddd;
    --band:#efefef;
    --card:#fafafa;
    --page:#ffffff;
    --negative:#e8474a;
    --photo-a:#4f6d5a;
    --photo-b:#9cc3c9;
  }
  *{box-sizing:border-box;margin:0;padding:0}
  html,body{width:849px;height:1200px;overflow:hidden;background:var(--page)}
  body{font-family:'Lato',sans-serif;color:var(--ink);position:relative}

  .agency-mark{position:absolute;left:45px;top:14px;width:70px;height:70px;border-radius:50%;background:#000}
  .agency-name{position:absolute;left:136px;top:40px;font-size:16px;font-weight:700;letter-spacing:.2px}
  .agency-name span{font-weight:300}

  .agent{position:absolute;right:202px;top:28px;text-align:right}
  .agent-name{color:var(--accent);font-size:16px;font-weight:700;letter-spacing:.2px}
  .agent-name span{font-weight:300}
  .agent-phone{font-size:11.5px;margin-top:5px;display:flex;justify-content:flex-end;align-items:center;gap:18px}
  .agent-email{font-size:11.5px;margin-top:7px}
  .agent-photo{position:absolute;left:682px;top:28px;width:114px;height:123px;border-radius:8px;
    background:linear-gradient(160deg,var(--photo-b),var(--photo-a));box-shadow:0 2px 6px rgba(0,0,0,.15)}

  .header-rule{position:absolute;left:38px;top:106px;width:775px;height:1px;background:var(--rule)}
  .header-rule-accent{position:absolute;left:38px;top:105px;width:273px;height:2.5px;background:var(--accent)}

  .property-title{position:absolute;left:39px;top:117px;font-size:24px;font-weight:700}
  .property-type{position:absolute;left:39px;top:147px;font-size:10px;font-weight:700;color:#222}
  .property-address{position:absolute;left:39px;top:168px;font-size:10px;font-weight:700;color:#222;display:flex;align-items:center;gap:9px}

  .section-title{position:absolute;left:40px;font-size:19px;color:var(--accent);font-weight:700}
  .section-title span{font-weight:300}

  .card{position:absolute;left:39px;width:774px;background:var(--card);border-radius:8px;
    box-shadow:0 1px 5px rgba(0,0,0,.12);padding:12px 24px 0 8px}
  .band{height:29px;background:var(--band);border-radius:5px;display:flex;align-items:center;
    padding-left:8px;font-size:12px;font-weight:400;letter-spacing:.1px}
  .band::before{content:"";width:4px;height:4px;border-radius:50%;background:var(--accent);margin-right:16px}
  .rows{margin-left:49px;margin-top:2px}
  .row{height:20.3px;border-bottom:1px solid var(--rule);display:flex;align-items:center;font-size:8.5px;color:var(--muted)}
  .row .label{flex:1}
  .row .mid{position:absolute;left:416px}
  .row .value{text-align:right}
  .negative{color:var(--negative)}
  .total{margin-left:369px;border-top:2px solid var(--accent);height:27px;display:flex;align-items:center;
    justify-content:space-between;font-size:12px;margin-top:-1px}
  .total .value{font-size:12px;font-weight:700}
  .spacer{height:0}

  .footer{position:absolute;left:38px;right:38px;top:1184px;display:flex;justify-content:space-between;font-size:8px;color:#333}
</style>
</head>
<body>
  <div class="agency-mark"></div>
  <div class="agency-name">AGENCYNAME <span>HERE</span></div>

  <div class="agent">
    <div class="agent-name">SALEMANS <span>NAME</span></div>
    <div class="agent-phone">
      <svg width="10" height="10" viewBox="0 0 24 24" fill="none" stroke="#111" stroke-width="2"><path d="M22 16.9v3a2 2 0 0 1-2.2 2 19.8 19.8 0 0 1-8.6-3.1 19.5 19.5 0 0 1-6-6A19.8 19.8 0 0 1 2.1 4.2 2 2 0 0 1 4.1 2h3a2 2 0 0 1 2 1.7c.1.9.4 1.8.7 2.7a2 2 0 0 1-.5 2.1L8 9.8a16 16 0 0 0 6 6l1.3-1.3a2 2 0 0 1 2.1-.4c.9.3 1.8.6 2.7.7a2 2 0 0 1 1.7 2z"/></svg>
      <span>(555) 214-0917</span>
    </div>
    <div class="agent-email">milo@harborlane.example</div>
  </div>
  <div class="agent-photo" role="img" aria-label="Agent headshot"></div>

  <div class="header-rule"></div>
  <div class="header-rule-accent"></div>

  <div class="property-title">412 FERNWOOD</div>
  <div class="property-type">15-Plex of 1bd/1bth Apartments</div>
  <div class="property-address">
    <svg width="9" height="11" viewBox="0 0 24 30"><path d="M12 0a11 11 0 0 0-11 11c0 8 11 19 11 19s11-11 11-19A11 11 0 0 0 12 0zm0 15a4 4 0 1 1 0-8 4 4 0 0 1 0 8z" fill="#111"/></svg>
    <span>15-Plex of 1bd/1bth Apartments</span>
  </div>

  <div class="section-title" style="top:238px">The Four <span>Benefits</span></div>
  <section class="card" style="top:269px;height:470px">
    <div class="band">CASH FLOW BEFOR TAX:</div>
    <div class="rows">
      <div class="row"><span class="label">Gross Operating Income</span><span class="value">$170.000</span></div>
      <div class="row"><span class="label">Operating Expenses</span><span class="value">$40.123</span></div>
      <div class="row"><span class="label">Net Operating Income</span><span class="value">$129.877</span></div>
      <div class="row"><span class="label">Annual Debt Service (Monthly P&amp;I x 12)</span><span class="value">$125.784</span></div>
    </div>
    <div class="total"><span>Chash flow befor tax:</span><span class="value">$4.092</span></div>

    <div class="band">PRINCIPAL REDUCTION:</div>
    <div class="rows">
      <div class="row"><span class="label">Annual Debt Service</span><span class="value">$125.784</span></div>
      <div class="row"><span class="label">Interest (first year)</span><span class="value negative">-$93.621</span></div>
    </div>
    <div class="total"><span>Chash flow befor tax:</span><span class="value">$32.163</span></div>

    <div class="band">TAXES PAID/SAVED:</div>
    <div class="rows">
      <div class="row"><span class="label">Net Operating Income</span><span class="value">$129.877</span></div>
      <div class="row"><span class="label">Interest paid in first year</span><span class="value">$93.621</span></div>
      <div class="row"><span class="label">Total Depreciation</span><span class="value">$55.168</span></div>
      <div class="row"><span class="label">Taxable Income</span><span class="value negative">-$18.912</span></div>
      <div class="row"><span class="label">Tax Bracket</span><span class="mid">28%</span><span class="value negative">-$5.295</span></div>
    </div>
    <div class="total"><span>Taxes Saved:</span><span class="value">$5.295</span></div>

    <div class="band">APPRECIATION:</div>
    <div class="rows"><div class="row" style="height:1px"></div></div>
    <div class="total"><span>Estimate of Appriciation:</span><span class="value">0%</span></div>
  </section>

  <div class="section-title" style="top:766px">Rates of <span>Returns</span></div>
  <section class="card" style="top:797px;height:323px">
    <div class="band">RETURN ON INVESTMENT WITHOUT APPRICIATION:</div>
    <div class="rows">
      <div class="row"><span class="label">Cash Flow before Tax + Principal Reduction + Tax Saved</span><span class="value">$30.961</span></div>
      <div class="row"><span class="label">Cash Invested</span><span class="value">$341.000</span></div>
    </div>
    <div class="total"><span>ROI w/o Appriciation</span><span class="value">9.08%</span></div>

    <div class="band">CAPITALIZATION RATE:</div>
    <div class="rows">
      <div class="row"><span class="label">Net Operating Income</span><span class="value">$129.877</span></div>
      <div class="row"><span class="label">Purchase Cost</span><span class="value">$1.690.000</span></div>
    </div>
    <div class="total"><span>Capitalization Rate:</span><span class="value">7.69%</span></div>

    <div class="band">CASH ON CASH:</div>
    <div class="rows">
      <div class="row"><span class="label">Cash Flow before Tax</span><span class="value">$4.092</span></div>
      <div class="row"><span class="label">Cash Invested</span><span class="value">$341.000</span></div>
    </div>
    <div class="total"><span>Cash On Cash:</span><span class="value">1.2%</span></div>
  </section>

  <footer class="footer">
    <span>412 Fernwood, REF #47v8487 by Harbor Lane Realty | Report available at www.harborlane.example. June 26th, 2023</span>
    <span>Page 2/2</span>
  </footer>
</body>
</html>
```